Redesign of business card for Cedar Ridge Mechanical

We are looking for a new design for our business cards for Cedar Ridge Mechanical. We are a plumbing & HVAC construction company, operating on the West Coast of Canada and USA. Logo attached.
Industry/Entity Type
Construction - Plumbing & HVAC
Contact Information for Business Card
Name, address, phone numbers, email, website address
Look and feel
Each slider illustrates characteristics of the customer's brand and the style your logo design should communicate.

```html
<!DOCTYPE html>
<html lang="en">
<head>
<meta charset="utf-8">
<title>Cedar Ridge Mechanical – Business Card</title>
<link href="https://fonts.googleapis.com/css2?family=Montserrat:wght@400;800&display=swap" rel="stylesheet">
<style>
  :root {
    --ink: #111111;
    --muted: #3a3a3a;
    --card: #ffffff;
    --backdrop: #e6e6e6;
  }
  * { margin: 0; padding: 0; box-sizing: border-box; }
  html, body { width: 1200px; height: 913px; overflow: hidden; }
  body {
    background: var(--backdrop);
    font-family: "Montserrat", sans-serif;
    color: var(--ink);
    position: relative;
  }
  .card {
    position: absolute;
    width: 620px;
    height: 354px;
    background: var(--card);
    border-radius: 26px;
    box-shadow: 0 6px 18px rgba(0,0,0,0.18);
    overflow: hidden;
  }
  .card--front { left: 60px; top: 70px; }
  .card--back { left: 520px; top: 480px; }

  .brand {
    display: flex;
    align-items: center;
    gap: 12px;
    font-weight: 800;
    text-transform: uppercase;
    color: var(--ink);
  }
  .brand__square { background: var(--ink); flex: none; }

  .card--front .brand {
    position: absolute; left: 0; right: 0; top: 0; bottom: 0;
    justify-content: center;
    font-size: 30px;
    letter-spacing: 1px;
  }
  .card--front .brand__square { width: 30px; height: 30px; }

  .card--back .brand--small {
    position: absolute; left: 38px; top: 44px;
    font-size: 16px; letter-spacing: 0.5px; gap: 9px;
  }
  .card--back .brand--small .brand__square { width: 16px; height: 16px; }

  .card--back .brand--large {
    position: absolute; right: 34px; top: 150px;
    flex-direction: column; align-items: flex-end; gap: 2px;
    font-size: 30px; line-height: 1.05; text-align: right;
  }

  .holder {
    position: absolute; right: 40px; top: 24px; text-align: right;
  }
  .holder__name { font-weight: 800; font-size: 21px; letter-spacing: 0.5px; }
  .holder__role { font-weight: 400; font-size: 14px; color: var(--muted); margin-top: 2px; }
  .edge-tab {
    position: absolute; right: 0; top: 22px; width: 14px; height: 50px; background: var(--ink);
  }

  .contact {
    position: absolute; left: 38px; bottom: 30px;
    font-size: 15px; color: var(--muted); line-height: 1.45;
  }
  .contact__address { margin-bottom: 12px; }
  .contact__row { display: flex; align-items: center; gap: 9px; }
  .contact__row svg { width: 13px; height: 13px; flex: none; }
</style>
</head>
<body>

  <section class="card card--front">
    <div class="brand"><span class="brand__square"></span>Cedar Ridge Mechanical</div>
  </section>

  <section class="card card--back">
    <span class="edge-tab"></span>
    <div class="holder">
      <div class="holder__name">DANIEL HALE</div>
      <div class="holder__role">Managing Director</div>
    </div>

    <div class="brand brand--small"><span class="brand__square"></span>Cedar Ridge Mechanical</div>

    <div class="brand brand--large">
      <span>Cedar Ridge</span>
      <span>Mechanical</span>
    </div>

    <div class="contact">
      <div class="contact__address">Your address,<br>City State, Zip 1234</div>
      <div class="contact__row">
        <svg viewBox="0 0 16 16" aria-hidden="true"><path fill="#111" d="M3 1l3 0 1 4-2 1c1 2 3 4 5 5l1-2 4 1v3c0 1-1 2-2 2C7 15 1 9 1 3c0-1 1-2 2-2z"/></svg>
        <span>123 456 789</span>
      </div>
      <div class="contact__row">
        <svg viewBox="0 0 16 16" aria-hidden="true"><rect x="1" y="3" width="14" height="10" fill="none" stroke="#111" stroke-width="1.6"/><path d="M1 3l7 6 7-6" fill="none" stroke="#111" stroke-width="1.6"/></svg>
        <span>info@yourgmail.com</span>
      </div>
      <div class="contact__row">
        <svg viewBox="0 0 16 16" aria-hidden="true"><circle cx="8" cy="8" r="7" fill="#111"/><path d="M1 8h14M8 1c3 3 3 11 0 14M8 1c-3 3-3 11 0 14" fill="none" stroke="#fff" stroke-width="1"/></svg>
        <span>www.yourwebsite.com</span>
      </div>
    </div>
  </section>

</body>
</html>
```